Business Broker Graphics Package

Hi,

Seeking a smart and professional graphics package design including business card design (double-sided) and letterhead and PowerPoint slide template.

3 Deliverables:

1. Company Letterhead
2. Business Card (two sided) (will consider one sided designs)
3. PowerPoint Template. Requires cover PPT and 2nd page design.

For the prototype use this info:
Marcus Dellorane RPA
Registered Practice Adviser
5678 Harlow Rd.
Ardmere, FL 70412
555.014.2273
Demo@Quillbrookpath.com
www.QuillbrookPath.com

I'll give exact information to winner to finalize later.

I've attached the logo..

Business card will be double sided and info for back of card is in attachment.

Look forward to your great ideas and concepts!

Target Market(s)

President's and business owners, CPA's and other professionals.

Industry/Entity Type

Business

Requirements
Nice to have
• Prefer horizontal card, but will consider vertical card design.

The business card should be all or primarily white. Text colors should be same as logo creative combination of black and forest green.

PowerPoint can be white background or lighter palette of colors I like gold color. I do not like darkly colored PowerPoint designs I prefer light and bright designs.

```html
<!DOCTYPE html>
<html lang="en">
<head>
<meta charset="utf-8">
<title>Business Card Back – Marcus Dellorane RPA</title>
<link rel="stylesheet" href="https://fonts.googleapis.com/css2?family=Tinos:ital,wght@0,400;0,700;1,400&display=swap">
<style>
  :root {
    --page-bg: #ececec;
    --forest: #006838;
    --ink: #0d0d0d;
    --outline: #231f20;
    --silver-light: #f2f2f2;
    --silver-mid: #d9d9d9;
    --silver-dark: #bdbdbd;
  }
  * { margin: 0; padding: 0; box-sizing: border-box; }
  html, body {
    width: 1200px; height: 1000px; overflow: hidden;
    background: var(--page-bg);
    font-family: "Tinos", "Times New Roman", serif;
    color: var(--ink);
  }
  .card {
    position: absolute; left: 58px; top: 126px;
    width: 1082px; height: 731px; overflow: hidden;
    background: linear-gradient(180deg, var(--silver-light) 40%, var(--silver-mid) 75%, var(--silver-dark) 100%);
  }
  .skyline-band {
    position: absolute; left: 0; top: 0; width: 1082px; height: 335px;
  }
  .identity {
    position: absolute; right: 173px; top: 350px; text-align: right;
  }
  .identity__name { font-weight: 700; font-size: 31px; line-height: 34px; letter-spacing: 0.3px; }
  .identity__title { font-style: italic; font-size: 21px; line-height: 22px; }
  .contact {
    position: absolute; right: 174px; top: 416px; list-style: none; text-align: right;
    font-size: 20px; line-height: 25px;
  }
  .contact__item { display: flex; justify-content: flex-end; align-items: flex-start; gap: 13px; }
  .contact__item svg { width: 18px; height: 18px; margin-top: 3px; flex: none; }
  .contact__item--address span { line-height: 17px; padding-top: 4px; }
  .services {
    position: absolute; right: 173px; top: 612px; text-align: right;
  }
  .services__heading { font-weight: 700; font-size: 19px; line-height: 22px; }
  .services__list { font-size: 16.5px; line-height: 18px; }
</style>
</head>
<body>
  <section class="card" aria-label="Business card back">
    <svg class="skyline-band" viewBox="0 0 1082 335" role="img" aria-label="City skyline silhouette with a black outline against a forest green sky">
      <rect x="0" y="0" width="1082" height="335" fill="var(--forest)"/>
      <rect x="0" y="300" width="1082" height="35" fill="var(--silver-light)"/>
      <rect x="0" y="294" width="1082" height="14" fill="var(--outline)"/>
    </svg>

    <header class="identity">
      <h1 class="identity__name">MARCUS DELLORANE RPA</h1>
      <p class="identity__title">Registered Practice Adviser</p>
    </header>

    <ul class="contact">
      <li class="contact__item"><span>555.014.2273</span>
        <svg viewBox="0 0 24 24" aria-hidden="true"><path fill="var(--ink)" d="M6.6 2.5 9.5 6.3c.4.6.3 1.4-.2 1.9L7.8 9.6c1.2 2.8 3.6 5.3 6.5 6.6l1.4-1.5c.5-.5 1.3-.6 1.9-.2l3.8 2.9c.6.5.7 1.3.2 1.9l-1.8 2.2c-.6.7-1.6 1-2.5.7C9.8 19.8 4.2 14.2 2.1 6.7c-.3-.9 0-1.9.7-2.5L4.7 2.3c.6-.5 1.4-.4 1.9.2Z"/></svg></li>
      <li class="contact__item"><span>Demo@Quillbrookpath.com</span>
        <svg viewBox="0 0 24 24" aria-hidden="true"><rect x="2" y="6" width="20" height="13" fill="var(--ink)"/><path d="M3 7l9 7 9-7" fill="none" stroke="var(--silver-light)" stroke-width="1.6"/></svg></li>
      <li class="contact__item"><span>www.QuillbrookPath.com</span>
        <svg viewBox="0 0 24 24" aria-hidden="true"><circle cx="12" cy="12" r="10" fill="var(--ink)"/><path d="M7 6c2 1 3 3 2 5s1 3 2 5M15 4c-1 2 1 3 3 3s2 3 1 5c-1 2-3 2-4 4" fill="none" stroke="var(--silver-light)" stroke-width="1.6"/></svg></li>
      <li class="contact__item contact__item--address"><span>5678 Harlow Rd.<br>Ardmere, FL 70412</span>
        <svg viewBox="0 0 24 24" aria-hidden="true"><path fill="var(--ink)" d="M12 2a7 7 0 0 0-7 7c0 5 7 13 7 13s7-8 7-13a7 7 0 0 0-7-7Zm0 10a3 3 0 1 1 0-6 3 3 0 0 1 0 6Z"/></svg></li>
    </ul>

    <footer class="services">
      <h2 class="services__heading">Harrowgate Advisory</h2>
      <p class="services__list">Business Sale - Acquisition - Exit Planning - Valuation - Growth Engineer</p>
    </footer>
  </section>
</body>
</html>
```